Calm Nest

I currently have a squarespace website www.bodysensepillow.comI want a complete design change but I want you to use the current information on the site.
Updates

We will be making a decision this week. Thank You.

```html
<!DOCTYPE html>
<html lang="en">
<head>
<meta charset="utf-8">
<title>Calm Nest</title>
<link rel="stylesheet" href="https://fonts.googleapis.com/css2?family=Montserrat:wght@700;800&family=Open+Sans:wght@300;400;600;700&family=Great+Vibes&display=swap">
<style>
:root{
  --ink:#333333;
  --ink-dark:#262626;
  --text:#555555;
  --muted:#8a8a8a;
  --panel:#3a3a3a;
  --footer:#333333;
  --footer-base:#2a2a2a;
  --light:#efefef;
  --line:#cfcfcf;
  --white:#ffffff;
}
*{margin:0;padding:0;box-sizing:border-box}
html,body{width:1200px;height:3583px;overflow:hidden;background:var(--white)}
body{position:relative;font-family:"Open Sans",sans-serif;color:var(--ink)}
.abs{position:absolute}
.heading{font-family:"Montserrat",sans-serif;font-weight:800;letter-spacing:1px}

.site-header{left:0;top:0;width:1200px;height:104px;background:var(--white)}
.brand{left:76px;top:34px;font-family:"Montserrat",sans-serif;font-weight:700;font-size:31px;color:var(--ink);letter-spacing:.5px}
.nav{right:78px;top:44px;display:flex;gap:26px;align-items:center;font-size:14px;color:#666}
.nav a{color:inherit;text-decoration:none}
.nav .active{color:var(--ink);position:relative}
.nav .active::before{content:"";position:absolute;left:0;top:-6px;width:16px;height:1px;background:var(--ink)}

.hero{left:0;top:104px;width:1200px;height:551px;background:linear-gradient(135deg,#8f8c8b 0%,#a9a3a0 35%,#b39a8e 55%,#7d7674 100%)}
.hero-title{left:0;top:318px;width:1200px;text-align:center;color:var(--white);font-size:40px;line-height:53px;letter-spacing:1.5px}

.about{left:0;top:655px;width:1200px;height:480px;background:var(--light);overflow:hidden}
.about h2{position:absolute;left:0;top:60px;width:1200px;text-align:center;font-size:38px;color:var(--ink)}
.about p{position:absolute;left:180px;width:840px;text-align:center;font-size:14.5px;line-height:25px;color:var(--text)}
.btn-outline{left:506px;top:296px;width:187px;height:50px;border:1.5px solid var(--ink);border-radius:3px;display:flex;align-items:center;justify-content:center;font-family:"Montserrat",sans-serif;font-weight:700;font-size:18px;color:var(--ink);letter-spacing:.5px}
.script-band{left:0;top:378px;width:1200px;text-align:center;font-family:"Great Vibes",cursive;font-size:110px;color:var(--white);line-height:1}

.cat-bar{background:var(--panel)}
.cat-label{font-family:"Montserrat",sans-serif;font-weight:800;font-size:46px;color:#111;white-space:nowrap;letter-spacing:1px}
.cat-script{font-family:"Great Vibes",cursive;font-size:52px;color:#6d6d6d;white-space:nowrap}
.cat-title{font-size:36px;font-weight:400;color:var(--ink);letter-spacing:1px}
.cat-item{font-size:14.5px;color:var(--text)}
.photo-pillow{left:199px;top:1250px;width:499px;height:353px;background:linear-gradient(160deg,#9a7b5a 0%,#6fb8d8 30%,#5fb0d6 55%,#a9aaa2 80%,#8d8d86 100%);clip-path:polygon(0 0,100% 0,100% 26.3%,84.8% 26.3%,84.8% 100%,0 100%)}
.photo-sheets{left:501px;top:1719px;width:499px;height:353px;background:linear-gradient(150deg,#8a7d70 0%,#c9c7c2 30%,#dcdad6 55%,#b9b7b2 80%,#9a9994 100%);clip-path:polygon(0 0,100% 0,100% 100%,15.2% 100%,15.2% 26.3%,0 26.3%)}

.products{left:0;top:2186px;width:1200px;height:520px;background:linear-gradient(100deg,#8c8c8c 0%,#b8b6b4 40%,#d9d8d6 60%,#a7a6a4 85%,#cfcecc 100%)}
.products-panel{left:76px;top:2186px;width:395px;height:520px;background:rgba(58,58,58,.94)}
.products-panel h2{position:absolute;left:0;top:106px;width:395px;text-align:center;color:var(--white);font-size:44px;line-height:49px}
.products-panel .item{position:absolute;left:0;width:395px;text-align:center;color:var(--white);font-size:14.5px}
.products-panel .rule{position:absolute;left:51px;width:303px;height:1px;background:#5c5c5c}

.contact-title{left:0;top:2752px;width:1200px;text-align:center;font-size:40px;color:var(--ink)}
.info-card{top:2834px;width:323px;height:165px;border:1px solid var(--line);text-align:center}
.info-card .icon{position:absolute;left:136px;top:33px;width:52px;height:52px;border:1px solid #bdbdbd;border-radius:50%;display:flex;align-items:center;justify-content:center}
.info-card .value{position:absolute;left:0;top:99px;width:321px;font-size:14.5px;color:var(--text)}
.field{height:1px;background:var(--line)}
.placeholder{font-size:14px;color:var(--muted)}
.btn-solid{left:506px;top:3220px;width:187px;height:52px;background:var(--ink);border-radius:3px;display:flex;align-items:center;justify-content:center;color:var(--white);font-family:"Montserrat",sans-serif;font-weight:700;font-size:17px;letter-spacing:1px}

.footer{left:0;top:3352px;width:1200px;height:169px;background:var(--footer)}
.footer-brand{left:0;top:42px;width:1200px;text-align:center;font-family:"Montserrat",sans-serif;font-weight:700;font-size:33px;color:var(--white)}
.footer-links{left:0;top:108px;width:1200px;display:flex;justify-content:center;gap:28px;font-size:14.5px;color:var(--white)}
.footer-base{left:0;top:3521px;width:1200px;height:62px;background:var(--footer-base);display:flex;align-items:center;justify-content:center;font-size:14px;color:#e0e0e0}
</style>
</head>
<body>

<header class="site-header abs">
  <div class="brand abs">CALM NEST</div>
  <nav class="nav abs">
    <a class="active">HOME</a><a>COMPANY</a><a>PILLOWS</a><a>SHEETS</a><a>CONTACT</a><a>PRODUCTS</a>
    <svg width="20" height="20" viewBox="0 0 20 20" aria-label="Search"><circle cx="8.5" cy="8.5" r="6" fill="none" stroke="#333" stroke-width="2"/><line x1="13" y1="13" x2="18" y2="18" stroke="#333" stroke-width="2.2" stroke-linecap="round"/></svg>
  </nav>
</header>

<section class="hero abs" role="img" aria-label="Photo of a woman sleeping peacefully on white bedding"></section>
<h1 class="hero-title heading abs">HELPING PEOPLE SLEEP BETTER IS THE<br>MOST IMPORTANT THING THAT WE DO.</h1>

<section class="about abs">
  <h2 class="heading">ABOUT US</h2>
  <p style="top:123px">Calm Nest believes that sleep is the most important part of your life. We created Calm Nest because better sleep makes for a better life. We carry a variety of speciality sleep products that are made with the finest materials available.</p>
  <p style="top:190px">We believe that having the correct pillow is essential to achieving the best night of sleep. Pillows play a vital role in supporting the intricate structures of the head, neck, shoulders, hips, and spine. Pillows can help alleviate or prevent many common forms of back and neck pain, as well as shoulder, hip and other forms of joint pain.</p>
  <div class="btn-outline abs">KNOW MORE</div>
  <div class="script-band abs">helping people sleep better</div>
</section>

<div class="cat-bar abs" style="left:106px;top:1250px;width:82px;height:353px"></div>
<div class="cat-script abs" style="left:152px;top:1340px;transform:translate(-50%,-50%) rotate(-90deg)">pillows</div>
<div class="cat-label abs" style="left:97px;top:1462px;transform:translate(-50%,-50%) rotate(-90deg)">PILLOWS</div>
<div class="photo-pillow abs" role="img" aria-label="Photo of blue textured pillows on a striped bed"></div>
<div class="cat-title abs" style="left:698px;top:1410px">PILLOWS</div>
<div class="cat-item abs" style="left:698px;top:1486px">Breeze Form</div>
<div class="cat-item abs" style="left:906px;top:1486px">Warm Haven</div>
<div class="cat-item abs" style="left:698px;top:1525px">Pure Rest</div>
<div class="cat-item abs" style="left:906px;top:1525px">Meadow Rest</div>

<div class="photo-sheets abs" role="img" aria-label="Photo of a bed with striped sheets and a tray"></div>
<div class="cat-bar abs" style="left:1011px;top:1719px;width:83px;height:353px"></div>
<div class="cat-script abs" style="left:1052px;top:1980px;transform:translate(-50%,-50%) rotate(90deg)">sheets</div>
<div class="cat-label abs" style="left:1103px;top:1845px;transform:translate(-50%,-50%) rotate(90deg)">SHEETS</div>
<div class="cat-title abs" style="left:153px;top:1866px">SHEETS</div>
<div class="cat-item abs" style="left:153px;top:1942px">Bamboo</div>
<div class="cat-item abs" style="left:153px;top:1983px">Cool</div>

<section class="products abs" role="img" aria-label="Photo of a made bed with grey and white striped cushions"></section>
<div class="products-panel abs">
  <h2 class="heading">PRODUCTS<br>2019</h2>
  <div class="item" style="top:250px">2019 Silver Birch Restful Bedding</div>
  <div class="rule" style="top:299px"></div>
  <div class="item" style="top:322px">2019 Woven Linens</div>
  <div class="rule" style="top:368px"></div>
  <div class="item" style="top:394px">2019 Chill Night Sleep Products</div>
</div>

<h2 class="contact-title heading abs">GET IN TOUCH</h2>
<div class="info-card abs" style="left:76px">
  <div class="icon"><svg width="20" height="20" viewBox="0 0 24 24"><path fill="#333" d="M6.6 10.8a15.1 15.1 0 0 0 6.6 6.6l2.2-2.2c.3-.3.7-.4 1-.2 1.1.4 2.3.6 3.6.6.6 0 1 .4 1 1V20c0 .6-.4 1-1 1A17 17 0 0 1 3 4c0-.6.4-1 1-1h3.5c.6 0 1 .4 1 1 0 1.3.2 2.5.6 3.6.1.3 0 .7-.2 1z"/></svg></div>
  <div class="value">123 456 7890</div>
</div>
<div class="info-card abs" style="left:438px">
  <div class="icon"><svg width="18" height="22" viewBox="0 0 18 22"><path fill="#333" d="M9 0a8 8 0 0 0-8 8c0 6 8 14 8 14s8-8 8-14a8 8 0 0 0-8-8zm0 11a3 3 0 1 1 0-6 3 3 0 0 1 0 6z"/></svg></div>
  <div class="value">Lorem Ipsum is simply dummy.</div>
</div>
<div class="info-card abs" style="left:800px">
  <div class="icon"><svg width="20" height="14" viewBox="0 0 20 14"><rect x="0.5" y="0.5" width="19" height="13" fill="#333"/><path d="M1 1l9 7 9-7" fill="none" stroke="#fff" stroke-width="1.2"/></svg></div>
  <div class="value">info@calmnest.example</div>
</div>

<div class="placeholder abs" style="left:99px;top:3071px">Your Name</div>
<div class="field abs" style="left:76px;top:3105px;width:325px"></div>
<div class="placeholder abs" style="left:460px;top:3071px">Your Email</div>
<div class="field abs" style="left:438px;top:3105px;width:325px"></div>
<div class="placeholder abs" style="left:822px;top:3071px">Your phone no.</div>
<div class="field abs" style="left:800px;top:3105px;width:325px"></div>
<div class="placeholder abs" style="left:99px;top:3165px">Your Message</div>
<div class="field abs" style="left:76px;top:3199px;width:1049px"></div>
<div class="btn-solid abs">SEND NOW</div>

<footer class="footer abs">
  <div class="footer-brand abs">CALM NEST</div>
  <div class="footer-links abs"><span>Home</span><span>|</span><span>Pillows</span><span>|</span><span>Sheets</span><span>|</span><span>Contact</span><span>|</span><span>Products</span></div>
</footer>
<div class="footer-base abs">2019 ©CALM NEST - All Rights Reserved.</div>

</body>
</html>
```